Emergency Management Consulting Needs a Website

Need to develop a website for an Emergency Management Consulting business. This website needs to be user friendly and resemble disaster preparedness, response, recovery, and mitigation. It must allow for me to make changes to it myself by adding pages, content and pictures. Looking for an advanced page to the website that allows monitoring of social media sites, hashtags, and keywords. Must have pictures of disasters on the site. Must try to integrate the logo colors, not excessive.

Reason: Did not receive anything sufficient to what I am looking for.

Industry/Entity Type

Government

Coding

Coded - Design and coding required

Number of Pages Required

5+ page

Requirements
Must have
• Logo, advanced social media monitoring page, allow for edits myself (content, pages, graphics) this must be a CMS of some sort, use logo color scheme (not excessively), must be professional looking, connect with Plivex Domain, find a hosting site, SEO, no "long" designs, minimize "dead" space, no social media feeds, no newsletter stuff.
• Menu items: Home, About Us, Services, Situation Monitor, Work With Us, Contact Us (hopefully these could be editable if I need to later)
• When you make a submission, please send me a message on which CMS you are using. Thank you.
Nice to have
• Examples of websites:
• https://www.qrt.vic.gov.au/
• http://www.larkenmoss.example/
• http://www.tulpaxo.example/
• http://vonmirelconsulting.example/
• http://www.calvornet.example/services/emergency-management
• https://zuq.example/
• http://www.vestimora.example/Responsibility/Sustainable-Development/HSE/Crisis-and-Emergency-Management/

```html
<!DOCTYPE html>
<html lang="en">
<head>
<meta charset="utf-8">
<title>Kestrel Vale Emergency Management</title>
<link href="https://fonts.googleapis.com/css2?family=Exo+2:wght@500;600;700&family=Open+Sans:wght@400;600&display=swap" rel="stylesheet">
<style>
:root{
  --blue:#0d5aa7;
  --blue-dark:#0a4584;
  --orange:#e8692a;
  --gold:#f2a516;
  --ink:#333a42;
  --muted:#8a9097;
  --band:#f7f7f7;
  --line:#e6e6e6;
  --white:#ffffff;
}
*{margin:0;padding:0;box-sizing:border-box}
html,body{width:1200px;height:3051px;overflow:hidden;background:var(--white)}
body{position:relative;font-family:"Open Sans",sans-serif;color:var(--ink)}
.abs{position:absolute}
h2{font-family:"Exo 2",sans-serif;font-weight:700;color:var(--blue);font-size:28px}

/* header */
.site-header{left:0;top:0;width:1200px;height:86px;background:var(--white)}
.brand{display:flex;align-items:center;gap:10px}
.brand-mark{width:26px;height:26px;border-radius:50%;background:var(--orange)}
.brand-name{font-family:"Exo 2",sans-serif;font-weight:700;font-size:20px;color:var(--blue-dark);letter-spacing:.5px}
.main-nav{left:506px;top:39px;display:flex;gap:19px;font-size:9.5px;font-weight:600;text-transform:uppercase;color:var(--ink);white-space:nowrap}
.main-nav .active{color:var(--orange)}
.search-btn{left:962px;top:30px;width:30px;height:30px;border-radius:50%;background:var(--blue);display:flex;align-items:center;justify-content:center}

/* hero */
.hero{left:0;top:86px;width:1200px;height:549px;overflow:hidden}
.hero-bg{inset:0;background:linear-gradient(120deg,#2a1f1a 0%,#3a2a22 45%,#1f1c1c 100%)}
.hero-photo{left:0;top:0;width:720px;height:549px;clip-path:polygon(0 0,437px 0,702px 100%,0 100%);background:linear-gradient(160deg,#d8d4cf 0%,#c9bfb5 40%,#d86a2a 60%,#6b4a33 100%)}
.hero-copy{left:677px;top:160px}
.hero-title{font-family:"Exo 2",sans-serif;font-weight:700;font-size:33px;color:var(--gold)}
.hero-sub{font-family:"Exo 2",sans-serif;font-weight:600;font-size:27px;line-height:34px;color:var(--white);margin-top:8px}
.btn{display:inline-block;background:var(--blue);color:var(--white);font-size:12px;font-weight:600;text-transform:uppercase;padding:13px 30px;margin-top:19px}
.hero-dots{left:1107px;top:296px;display:flex;flex-direction:column;gap:14px}
.hero-dots span{width:8px;height:8px;border-radius:50%;background:var(--white)}
.hero-dots .on{background:var(--blue)}

/* provide */
.provide-head{left:199px;top:758px}
.provide-text{left:199px;top:832px;width:330px;font-size:13px;line-height:18.5px;color:var(--ink)}
.provide-text p+p{margin-top:17px}
.tile{width:196px;height:182px;background:linear-gradient(160deg,#4d8ccc,#1f67b0);color:var(--white)}
.tile svg{position:absolute;left:22px;top:92px}
.tile-label{position:absolute;left:20px;bottom:14px;font-family:"Exo 2",sans-serif;font-weight:600;font-size:19px}

/* news */
.news-band{left:0;top:1190px;width:1200px;height:545px;background:var(--band)}
.section-head{width:1200px;left:0;text-align:center}
.news-card{width:250px}
.news-photo{width:250px;height:199px}
.news-date{font-family:"Exo 2",sans-serif;font-weight:600;font-size:18px;color:var(--orange);margin-top:40px}
.news-text{font-size:13px;line-height:18.5px;margin-top:8px}

/* situation monitor */
.alert-card{width:391px;height:118px;background:var(--white);box-shadow:0 1px 6px rgba(0,0,0,.08)}
.alert-photo{position:absolute;left:18px;top:8px;width:104px;height:100px}
.level-badge{position:absolute;left:0;bottom:0;width:20px;height:20px;background:var(--blue)}
.alert-title{position:absolute;left:138px;top:10px;font-size:13px;color:var(--blue)}
.alert-text{position:absolute;left:138px;top:42px;width:212px;font-size:10px;line-height:18px;color:var(--ink)}
.alert-icons{position:absolute;right:18px;top:12px;display:flex;flex-direction:column;gap:6px}

/* testimonials */
.quote-band{left:0;top:2404px;width:1200px;height:354px;background:var(--band)}
.avatar-ring{left:512px;top:2326px;width:176px;height:176px;border-radius:50%;background:var(--white);box-shadow:0 2px 8px rgba(0,0,0,.08)}
.avatar{left:524px;top:2338px;width:152px;height:152px;border-radius:50%;background:linear-gradient(180deg,#c9cdd1,#9ea4aa)}
.person-name{font-family:"Exo 2",sans-serif;font-weight:600;font-size:18px;color:var(--orange)}
.person-role{font-size:12px;color:var(--muted)}
.quote{left:230px;top:2600px;width:740px;text-align:center;font-size:13.5px;line-height:20px}
.quote-dots{left:568px;top:2714px;display:flex;gap:12px}
.quote-dots span{width:7px;height:7px;border-radius:50%;background:#dde1e5}
.quote-dots .on{background:var(--blue)}

/* footer */
.foot-col h3{font-family:"Exo 2",sans-serif;font-weight:600;font-size:14px;color:var(--orange);margin-bottom:22px}
.foot-col li{list-style:none;font-size:10.5px;line-height:20px}
.legal-bar{left:0;top:3000px;width:1200px;height:51px;border-top:1px solid var(--line)}
.legal{left:199px;top:17px;font-size:10.5px;font-weight:600}
.connect{left:866px;top:15px;display:flex;align-items:center;gap:10px;font-size:10px;font-weight:600}
.connect span.dot{width:9px;height:9px;border-radius:50%;background:var(--blue)}
.connect span.dot.soft{background:#c9d1da}
.lang{left:1170px;top:16px;font-size:10px;font-weight:600}
</style>
</head>
<body>

<header class="site-header abs">
  <div class="brand abs" style="left:203px;top:28px"><span class="brand-mark"></span><span class="brand-name">KESTREL VALE</span></div>
  <nav class="main-nav abs">
    <span class="active">&#9733; Home</span><span>About Us</span><span>Services</span><span>Situation Monitor</span><span>Work With Us</span><span>Contact Us</span>
  </nav>
  <div class="search-btn abs"><svg width="13" height="13" viewBox="0 0 13 13"><circle cx="5.5" cy="5.5" r="4" fill="none" stroke="#fff" stroke-width="1.8"/><line x1="8.5" y1="8.5" x2="12" y2="12" stroke="#fff" stroke-width="1.8"/></svg></div>
</header>

<section class="hero abs">
  <div class="hero-bg abs" role="img" aria-label="Dark smoke and fire backdrop"></div>
  <div class="hero-photo abs" role="img" aria-label="Firefighters spraying water at a blaze"></div>
  <div class="hero-copy abs">
    <div class="hero-title">KESTREL VALE</div>
    <div class="hero-sub">Emergency Management<br>Consulting company</div>
    <a class="btn">Learn More</a>
  </div>
  <div class="hero-dots abs"><span class="on"></span><span></span><span></span><span></span></div>
</section>

<section>
  <h2 class="provide-head abs">What We Provide ?</h2>
  <div class="provide-text abs">
    <p>Sed ut perspiciatis unde omnis iste natus error sit voluptatem accusantium doloremque laudantium, totam rem aperiam, eaque ipsa quae ab illo inventore veritatis et quasi architecto beatae vitae dicta sunt explicabo. Nemo enim</p>
    <p>Sed ut perspiciatis unde omnis iste natus error sit voluptatem accusantium doloremque laudantium, totam rem aperiam, eaque ipsa quae ab illo inventore veritatis et quasi architecto beatae vitae dicta sunt explicabo.</p>
  </div>
  <div class="tile abs" style="left:596px;top:714px" role="img" aria-label="Responders training, blue tint">
    <svg width="48" height="44" viewBox="0 0 48 44"><rect x="2" y="8" width="44" height="34" rx="4" fill="none" stroke="#fff" stroke-width="3"/><path d="M17 8V3h14v5" fill="none" stroke="#fff" stroke-width="3"/><path d="M21 17h6v6h6v6h-6v6h-6v-6h-6v-6h6z" fill="#fff"/></svg>
    <span class="tile-label">Preparedness</span></div>
  <div class="tile abs" style="left:803px;top:714px" role="img" aria-label="Rescue helicopter, blue tint">
    <svg width="48" height="44" viewBox="0 0 48 44"><path d="M10 36V22a14 14 0 0 1 28 0v14z" fill="none" stroke="#fff" stroke-width="3"/><rect x="4" y="36" width="40" height="6" fill="#fff"/><path d="M24 2v5M6 9l4 4M42 9l-4 4" stroke="#fff" stroke-width="3"/></svg>
    <span class="tile-label">Response</span></div>
  <div class="tile abs" style="left:596px;top:907px" role="img" aria-label="Emergency vehicles, blue tint">
    <svg width="48" height="44" viewBox="0 0 48 44"><path d="M4 16h10l22-12v36L14 28H4z" fill="#fff"/><path d="M10 28l4 12h6l-3-12" fill="#fff"/><path d="M40 16h6M40 22h6" stroke="#fff" stroke-width="3"/></svg>
    <span class="tile-label">Recovery</span></div>
  <div class="tile abs" style="left:803px;top:907px" role="img" aria-label="Flood scene, blue tint">
    <svg width="48" height="44" viewBox="0 0 48 44"><path d="M24 3L3 22h6v19h30V22h6z" fill="#fff"/><path d="M24 18c-4 6-6 9-6 12a6 6 0 0 0 12 0c0-3-2-6-6-12z" fill="#2a6fb5"/></svg>
    <span class="tile-label">Mitigation</span></div>
</section>

<section>
  <div class="news-band abs"></div>
  <h2 class="section-head abs" style="top:1243px">Featured News</h2>
  <article class="news-card abs" style="left:199px;top:1322px">
    <div class="news-photo" role="img" aria-label="Aircraft cabin with exit sign" style="background:linear-gradient(135deg,#6d5a55,#c98c6a 60%,#f0b27a)"></div>
    <div class="news-date">March 15th 2017</div>
    <p class="news-text">Et quasi architecto beatae vitae dicta sunt explicabo. Nemo enim ipsam voluptatem quia voluptas</p>
  </article>
  <article class="news-card abs" style="left:472px;top:1322px">
    <div class="news-photo" role="img" aria-label="Paramedics at an open ambulance" style="background:linear-gradient(135deg,#5e7a3a,#b7a14a 50%,#8a3a2a)"></div>
    <div class="news-date">March 15th 2017</div>
    <p class="news-text">Et quasi architecto beatae vitae dicta sunt explicabo. Nemo enim ipsam voluptatem quia voluptas</p>
  </article>
  <article class="news-card abs" style="left:744px;top:1322px">
    <div class="news-photo" role="img" aria-label="White ambulance with red markings" style="background:linear-gradient(135deg,#b8413a,#e8e4e0 55%,#c9ccd0)"></div>
    <div class="news-date">March 15th 2017</div>
    <p class="news-text">Et quasi architecto beatae vitae dicta sunt explicabo. Nemo enim ipsam voluptatem quia voluptas</p>
  </article>
</section>

<section>
  <h2 class="section-head abs" style="top:1814px"># Situation Monitor</h2>

  <div class="alert-card abs" style="left:199px;top:1910px">
    <div class="alert-photo" role="img" aria-label="Rescue worker in red" style="background:linear-gradient(135deg,#c8372f,#e9e4e0)"><span class="level-badge"></span></div>
    <div class="alert-title">#wildfire keyword on Channel A</div>
    <p class="alert-text">Monitor flagged a rise in mentions near the east ridge. 48 reports in one hour, team review is now under way</p>
    <div class="alert-icons"><svg width="10" height="9" viewBox="0 0 10 9"><path d="M5 9L1 5a2.4 2.4 0 0 1 4-3 2.4 2.4 0 0 1 4 3z" fill="#0d5aa7"/></svg><svg width="10" height="9"><rect x="1" y="1" width="8" height="6" fill="none" stroke="#c9ccd0"/></svg><svg width="10" height="9"><path d="M1 1h5l3 4-3 3H1z" fill="none" stroke="#c9ccd0"/></svg></div>
  </div>
  <div class="alert-card abs" style="left:610px;top:1910px">
    <div class="alert-photo" role="img" aria-label="Emergency department entrance" style="background:linear-gradient(135deg,#b8342c,#d9d4d0)"><span class="level-badge"></span></div>
    <div class="alert-title">#evacuation keyword on Channel B</div>
    <p class="alert-text">Monitor flagged road closure talk on the north route. 22 reports in one hour, shelter partners have been notified</p>
    <div class="alert-icons"><svg width="10" height="9" viewBox="0 0 10 9"><path d="M5 9L1 5a2.4 2.4 0 0 1 4-3 2.4 2.4 0 0 1 4 3z" fill="#0d5aa7"/></svg><svg width="10" height="9"><rect x="1" y="1" width="8" height="6" fill="none" stroke="#c9ccd0"/></svg><svg width="10" height="9"><path d="M1 1h5l3 4-3 3H1z" fill="none" stroke="#c9ccd0"/></svg></div>
  </div>
  <div class="alert-card abs" style="left:199px;top:2058px">
    <div class="alert-photo" role="img" aria-label="Hand holding a phone" style="background:linear-gradient(135deg,#d9c7b8,#a36a56)"><span class="level-badge"></span></div>
    <div class="alert-title">#flood keyword on Channel C</div>
    <p class="alert-text">Monitor flagged rising water posts along the lower river. 31 reports in one hour, field crews are on standby now</p>
    <div class="alert-icons"><svg width="10" height="9" viewBox="0 0 10 9"><path d="M5 9L1 5a2.4 2.4 0 0 1 4-3 2.4 2.4 0 0 1 4 3z" fill="#0d5aa7"/></svg><svg width="10" height="9"><rect x="1" y="1" width="8" height="6" fill="none" stroke="#c9ccd0"/></svg><svg width="10" height="9"><path d="M1 1h5l3 4-3 3H1z" fill="none" stroke="#c9ccd0"/></svg></div>
  </div>
  <div class="alert-card abs" style="left:610px;top:2058px">
    <div class="alert-photo" role="img" aria-label="Phone in a car" style="background:linear-gradient(135deg,#3d4348,#b9bcbf)"><span class="level-badge"></span></div>
    <div class="alert-title">#outage keyword on Channel C</div>
    <p class="alert-text">Monitor flagged power loss reports in the west district. 17 reports in one hour, utility contact has been made</p>
    <div class="alert-icons"><svg width="10" height="9" viewBox="0 0 10 9"><path d="M5 9L1 5a2.4 2.4 0 0 1 4-3 2.4 2.4 0 0 1 4 3z" fill="#0d5aa7"/></svg><svg width="10" height="9"><rect x="1" y="1" width="8" height="6" fill="none" stroke="#c9ccd0"/></svg><svg width="10" height="9"><path d="M1 1h5l3 4-3 3H1z" fill="none" stroke="#c9ccd0"/></svg></div>
  </div>
</section>

<section>
  <h2 class="section-head abs" style="top:2262px">Testimonials</h2>
  <div class="quote-band abs"></div>
  <div class="avatar-ring abs"></div>
  <div class="avatar abs" role="img" aria-label="Portrait of the client"></div>
  <div class="section-head abs" style="top:2526px">
    <div class="person-name">Dorian Vell</div>
    <div class="person-role">Emergency Support Manager</div>
  </div>
  <p class="quote abs">Sed ut perspiciatis unde omnis iste natus error sit voluptatem accusantium doloremque laudantium, totam rem aperiam, eaque ipsa quae ab illo inventore veritatis et quasi architecto beatae vitae dicta sunt explicabo. Nemo enim Sed ut perspiciatis unde omnis iste natus error sit voluptatem accusantium doloremque laudantium</p>
  <div class="quote-dots abs"><span class="on"></span><span></span><span></span><span></span></div>
</section>

<footer>
  <div class="brand abs" style="left:203px;top:2823px"><span class="brand-mark"></span><span class="brand-name">KESTREL VALE</span></div>
  <div class="foot-col abs" style="left:454px;top:2822px"><h3>Other Links</h3><ul><li>Our Approach</li><li>Products</li><li>Services</li><li>Education and Training</li></ul></div>
  <div class="foot-col abs" style="left:657px;top:2822px"><h3>Research &amp; Resources</h3><ul><li>Research and Testing</li><li>Harlow Mutual Data Sheets</li><li>Standards and Certification</li><li>Tools and Resources</li></ul></div>
  <div class="foot-col abs" style="left:862px;top:2822px"><h3>News</h3><ul><li>Events</li><li>News Releases</li><li>In the News</li><li>Meet Our Experts</li><li>Press</li></ul></div>
  <div class="legal-bar abs">
    <div class="legal abs">&copy; 2017 Company Name &nbsp;|&nbsp; All Rights Reserved</div>
    <div class="connect abs">Connect with us <span class="dot"></span><span class="dot soft"></span><span class="dot soft"></span></div>
    <div class="lang abs">CS</div>
  </div>
</footer>

</body>
</html>
```